Wordpress Theme for Medical Clinics

** Please view updated Sitemap2.pdf doc to clarify some confusion ***

This is a multiuser WordPress subscription site for medical clinics. Please see attachment for sitemap. Please do not include extra content like social media icons, search bars, or images. If you have questions, please ask for clarification.
The site contains the following pages and sub-pages:

1. Home
2. Our Clinic
2a. Our Clinic > Mission
2b. Our Clinic > Services
2c. Our Clinic > Clinic Policies
2d. Our Clinic > Schedules
3. Our Staff
3a. Our Staff > [Staff member page]
4. Resources
4a. Resources > Patient Health (index)
4b. Resources > Patient Health (index) > [post]
4c. Resources > Links
4d. Resources > Forms
5. Alerts
5a. Alerts > [Alert Page]
6. Contact Us

Includes the Following Pages, Subpages, and Content
1. Home
a. About Us
b. Our Staff
c. Bulletins
d. Accepting New Patients (shown as an alert widget)
e. Links
i. Physician Toolbox
ii. Book an Appointment
f. Clinic Policies
i. Show first 3 policies (e.g. Late Arrivals, Missed Appointments, Fees)
ii. Link to Clinic Policies page
g. Primary widget (displayed on all pages)
i. Hours of operation
ii. Contact Info
1. Tel
2. Fax
3. Email
4. Address
5. Get directions (link to Google Maps)
2. Our Clinic
a. Main Page
i. Clinic Name
ii. Overview
iii. Languages Spoken
iv. Secondary Navigation
1. Mission
2. Services
3. Clinic Policies
4. Schedules (see attachment)
b. Our Clinic > Mission
c. Our Clinic > Services
i. For each service include service TITLE and DESCRIPTION
d. Our Clinic > Clinic Policies
i. For each policy include policy TITLE and DESCRIPTION
ii. Include the following policies in mockup
1. Late arrivals
2. Missed appointments
3. Fees for missed appointments
4. Referrals and follow-ups
5. Services not covered by RDA
6. Information for LTF patients
7. Medical Legal Reports
e. Our Clinic > Schedules
3. Our Staff
a. Main Page
i. Display a list of staff members. Include NAME and DESIGNATION
b. Our Staff > [Staff Name]
i. Include NAME, PICTURE, DESIGNATION, and BIO
4. Resources
a. Resources > Patient Health
i. Main Page
1. Posts (ordered by date)
a. Title
b. Summary
2. Side Navigation
a. Post Categories
ii. Patient Health > [post title]
1. Title
2. Post Category
3. Date
4. Author
5. Summary
6. Body
b. Resources > Links
1. Secondary Navigation - Categories
a. Sample Categories:
i. Local Services
ii. RDA and Drug Coverage
iii. Mental Health Resources
2. Category page
a. Include the following links in the 'Local Services' category
i. Hypertension clinics
ii. Home Care services
iii. Vaccine Clinics
c. Resources > Forms
i. Display a table with form TITLE and CATEGORY
ii. Side Navigation
1. Form Categories
a. Use the following sample Categories
i. Referrals
ii. Insurance
iii. Intake
iv. Discharge
v. Waivers
5. Alerts
a. Main page
i. List of all Alert posts
1. Include post TITLE as a link to the post
ii. Side Navigation
1. Alerts Archive
a. shown as Month + Number of posts
iii. Alerts > [Alert page]
1. Include TITLE, DATE, AUTHOR, BODY
6. Contact Us
a. Map
b. Hours of operation
c. Address
d. Phone number
e. Fax number
e. Fax number
f. Map
g. Email

Design notes:
- fixed width
- responsive (need designs for mobile, tablet, and desktop)
- simple, dark font, white background
- use Font Awesome icons where needed
- user adds own logo

Target Market(s)

Medical Clinics

Industry/Entity Type

Medical

Number of Pages Required

5+ page

Font styles to use
Serif
Sans Serif

Requirements
Must have
• Please keep designs very simple.
• Examples:
• https://www.quolbin.com/install
• http://www.ventrohax.com/company/about-us
• http://brindlequota.org/
• http://www.trosk.com/
Should not have
• Minimal or no use of shadows and gradients

```html
<!DOCTYPE html>
<html lang="en">
<head>
<meta charset="utf-8">
<title>Medical Clinics – Home</title>
<link href="https://fonts.googleapis.com/css2?family=Lato:wght@300;400;700&display=swap" rel="stylesheet">
<style>
:root{
  --blue:#0a8ee6;
  --blue-mid:#0a84d8;
  --blue-deep:#0878c9;
  --ink:#333;
  --muted:#777;
  --line:#dcdcdc;
  --panel:#f4f4f4;
  --footer:#2b2b2b;
  --footer-text:#8a8a8a;
}
*{margin:0;padding:0;box-sizing:border-box}
html,body{width:960px;height:1200px;overflow:hidden;background:#fff}
body{font-family:"Lato",Arial,sans-serif;color:var(--ink);position:relative}
.abs{position:absolute}
a{color:inherit;text-decoration:none}

.topbar{left:0;top:0;width:960px;height:24px;background:var(--blue);color:#fff;font-size:7px}
.topbar .help{left:129px;top:8px}
.topbar .links{right:129px;top:8px;display:flex;gap:6px}
.topbar .links span+span{border-left:1px solid #fff;padding-left:6px}

.header{left:0;top:24px;width:960px;height:66px}
.brand{left:129px;top:20px;display:flex;align-items:center;gap:10px;font-size:18px;font-weight:400;color:var(--ink)}
.brand .dot{width:20px;height:20px;border-radius:50%;background:var(--blue)}
.nav a{position:absolute;top:29px;font-size:8.5px;color:var(--ink)}
.nav .active{left:444px;top:0;width:48px;height:66px;background:var(--blue);color:#fff;text-align:center;padding-top:29px}

.hero{left:129px;top:90px;width:702px;height:240px;background:linear-gradient(90deg,#8a6a52 0%,#c9b8a6 35%,#e7ecef 60%,#dfe6ea 100%)}
.hero h1{position:absolute;left:28px;top:56px;font-weight:300;font-size:22px;line-height:26px;color:#fff}
.hero h1 span{color:var(--blue)}
.hero p{position:absolute;left:28px;top:118px;width:200px;font-size:7.5px;line-height:11px;color:#fff}
.hero .btn{position:absolute;left:28px;top:160px;width:107px;height:24px;background:var(--blue);color:#fff;font-size:8px;font-weight:700;line-height:24px;text-align:center}
.dots{position:absolute;left:35px;top:221px;display:flex;gap:3px}
.dots i{width:6px;height:6px;border-radius:50%;background:#fff}
.dots i.on{background:var(--blue)}
.arrow{width:21px;height:22px;background:var(--blue);display:flex;align-items:center;justify-content:center}

.info{top:330px;height:120px;color:#fff}
.info h3{font-size:11.5px;font-weight:400;line-height:14px;margin-bottom:8px}
.info.c1{left:129px;width:233px;background:var(--blue);padding:11px 19px}
.info.c2{left:362px;width:234px;background:var(--blue-mid);padding:11px 24px}
.info.c3{left:596px;width:235px;background:var(--blue-deep);padding:11px 25px}
.info .lead{font-size:11px;line-height:14px}
.info .cbtn{position:absolute;left:66px;top:61px;width:102px;height:24px;background:#fff;color:var(--blue);font-size:12px;text-align:center;line-height:24px}
.info table{font-size:8px;border-collapse:collapse}
.info td{line-height:11.4px;vertical-align:top;padding:0}

.about-img{left:129px;top:474px;width:161px;height:185px;border:1px solid var(--line);background:linear-gradient(180deg,#f2f2f2,#e4e4e4)}
.about{left:310px;top:480px;width:276px}
.about h2{font-size:13px;font-weight:400;margin-bottom:8px}
.about h4{font-size:9px;font-weight:400;margin-bottom:10px}
.about p{font-size:7.5px;line-height:12px;color:var(--muted);margin-bottom:12px}
.about .btn{display:inline-block;width:60px;height:22px;background:var(--blue);color:#fff;font-size:7.5px;font-weight:700;text-align:center;line-height:22px}

.policies{left:609px;top:474px;width:222px;height:185px;border:1px solid var(--line)}
.policies h3{height:26px;background:var(--blue);color:#fff;font-size:12px;font-weight:400;text-align:center;line-height:26px}
.policies ul{list-style:none;margin:8px 31px 0 26px}
.policies li{font-size:7.5px;color:var(--blue-deep);height:16.8px;line-height:16.8px;border-bottom:1px solid #eee}
.policies li:last-child{border:0}
.policies .btn{position:absolute;left:80px;top:155px;width:60px;height:18px;background:var(--blue);color:#fff;font-size:8px;text-align:center;line-height:18px}

.staff{left:0;top:683px;width:960px;height:336px;background:var(--panel)}
.staff h2{position:absolute;left:129px;top:22px;font-size:13px;font-weight:700}
.staff .sub{position:absolute;left:129px;top:45px;font-size:8.5px;color:var(--muted)}
.card{top:73px;width:162px;height:192px;background:#fff;border:1px solid var(--line)}
.card .ph{height:150px;background:linear-gradient(180deg,#fafafa,#e9eef2);border-bottom:1px solid var(--line)}
.card h4{font-size:11px;font-weight:400;line-height:14px;margin:7px 0 3px 5px}
.card span{display:block;font-size:9px;line-height:12px;color:var(--blue);margin-left:5px}
.sbtn{top:283px;height:27px;background:var(--blue);color:#fff;font-size:9.5px;text-align:center;line-height:27px}

.rule{left:0;top:1019px;width:960px;height:3px;background:var(--blue)}
.footer{left:0;top:1022px;width:960px;height:178px;background:var(--footer);color:var(--footer-text)}
.footer .brand{left:129px;top:24px;color:#fff}
.footer .brand .dot{background:#fff}
.footer .blurb{position:absolute;left:129px;top:70px;width:170px;font-size:7px;line-height:11px;color:#ccc}
.footer h5{font-size:11px;font-weight:400;color:#9a9a9a;margin-bottom:8px}
.footer ul{list-style:none;font-size:8px;line-height:14.4px}
.footer .col{top:24px}
.footer .ct td{font-size:8px;line-height:12px;vertical-align:top;padding-right:22px}
.footer .bottom{position:absolute;left:129px;top:150px;width:702px;border-top:1px solid #3b3b3b;padding-top:8px;font-size:8px}
.footer .bottom .mid{position:absolute;left:241px;top:8px;display:flex;gap:16px}
</style>
</head>
<body>

<div class="abs topbar">
  <span class="abs help">To help Here : 111 480 7261 &nbsp;|&nbsp; Email : hello@cedarwell.ca</span>
  <div class="abs links"><span>Book an Appointment</span><span>Physician Toolbox</span></div>
</div>

<header class="abs header">
  <div class="abs brand"><i class="dot"></i>Medical Clinics</div>
  <nav class="nav">
    <a class="active">Home</a>
    <a style="left:511px">Our Clinic</a>
    <a style="left:581px">Newsletter</a>
    <a style="left:654px">Our Staff</a>
    <a style="left:721px">Resources</a>
    <a style="left:790px">Contact Us</a>
  </nav>
</header>

<section class="abs hero" role="img" aria-label="Photo of a smiling team of doctors and nurses in a hospital corridor">
  <h1>We Care About<br><span>Every Patients</span></h1>
  <p>Lorem Ipsum is simply dummy text of the printing and typesetting industry. Lorem Ipsum has been the industry's standard dummy</p>
  <a class="btn">Make an Appointment</a>
  <div class="dots"><i></i><i></i><i class="on"></i><i></i></div>
</section>
<div class="abs arrow" style="left:118px;top:190px"><svg width="6" height="8"><path d="M5 0L1 4l4 4" stroke="#fff" fill="none"/></svg></div>
<div class="abs arrow" style="left:821px;top:190px"><svg width="6" height="8"><path d="M1 0l4 4-4 4" stroke="#fff" fill="none"/></svg></div>

<section class="abs info c1">
  <h3>New Patients</h3>
  <div class="lead">Accepting new Patients here...</div>
  <a class="cbtn">Contact Us</a>
</section>
<section class="abs info c2">
  <h3>Hours of Opration</h3>
  <table>
    <tr><td style="width:109px">Monday :</td><td>8:00 AM - 6:00 PM</td></tr>
    <tr><td>Tuesday :</td><td>8:00 AM - 6:00 PM</td></tr>
    <tr><td>Wednessday :</td><td>8:00 AM - 6:00 PM</td></tr>
    <tr><td>Thursday :</td><td>8:00 AM - 6:00 PM</td></tr>
    <tr><td>Friday :</td><td>8:00 AM - 6:00 PM</td></tr>
    <tr><td>Saturday :</td><td>9:00 AM - 4:00 PM</td></tr>
    <tr><td>Sunday :</td><td>9:00 AM - 4:00 PM</td></tr>
  </table>
</section>
<section class="abs info c3">
  <h3>Contact Info</h3>
  <table>
    <tr><td style="width:65px">Telephone :</td><td>604-555-0192</td></tr>
    <tr><td>Email:</td><td>hello@cedarwell.ca</td></tr>
    <tr><td>Address:</td><td>48 Alder Lane Kelton,B.<br>Canada, V2K 4RT</td></tr>
  </table>
</section>

<div class="abs about-img" role="img" aria-label="Photo of a smiling doctor holding a clipboard and pen"></div>
<section class="abs about">
  <h2>About Us</h2>
  <h4>Lorem Ipsum is simply dummy text of the printing</h4>
  <p>Lorem Ipsum is simply dummy text of the printing and typesetting industry. Lorem Ipsum has been the industry's standard dummy text ever since the 1500s, when an unknown printer took a galley of type and scrambled it to make a type specimen book. It has survived not only five centuries, but also the leap into electronic typesetting, remaining essentially unchanged.</p>
  <p>Lorem Ipsum is simply dummy text of the printing and typesetting industry. Lorem Ipsum has been the industry's standard dummy text ever since the 1500s, when an unknown.</p>
  <a class="btn">Read more</a>
</section>

<aside class="abs policies">
  <h3>Clinic Policies</h3>
  <ul>
    <li>Clinic Policies</li>
    <li>Late arrivals</li>
    <li>Missd appoinmets</li>
    <li>Fees for missed Appoinments</li>
    <li>Referrals and follow-ups</li>
    <li>Services not covered by RDA</li>
    <li>Medical Legal Reports</li>
  </ul>
  <a class="btn">View All <svg width="9" height="6"><path d="M0 3h8M5 0l3 3-3 3" stroke="#fff" fill="none"/></svg></a>
</aside>

<section class="abs staff">
  <h2>Our Staff</h2>
  <div class="sub">Lorem Ipsum is simply dummy text of the printingorem Ipsum is simply dummy text of the printing</div>
  <div class="abs card" style="left:129px"><div class="ph" role="img" aria-label="Portrait photo of a female doctor"></div><h4>Dr. Mara Ellison</h4><span>Pediatric Clinic</span></div>
  <div class="abs card" style="left:309px"><div class="ph" role="img" aria-label="Portrait photo of a male doctor"></div><h4>Dr. Owen Pratley</h4><span>Cardiac Clinic</span></div>
  <div class="abs card" style="left:489px"><div class="ph" role="img" aria-label="Portrait photo of a female therapist in scrubs"></div><h4>Dr. Lena Corvath</h4><span>Rehabilitation Therapy</span></div>
  <div class="abs card" style="left:669px"><div class="ph" role="img" aria-label="Portrait photo of a male doctor"></div><h4>Dr. Tobias Reane</h4><span>Laryngological Clinic</span></div>
  <div class="abs arrow" style="left:103px;top:155px"><svg width="6" height="8"><path d="M5 0L1 4l4 4" stroke="#fff" fill="none"/></svg></div>
  <div class="abs arrow" style="left:837px;top:155px"><svg width="6" height="8"><path d="M1 0l4 4-4 4" stroke="#fff" fill="none"/></svg></div>
  <a class="abs sbtn" style="left:384px;width:72px">View All</a>
  <a class="abs sbtn" style="left:462px;width:114px">Staff Schedule</a>
</section>

<div class="abs rule"></div>
<footer class="abs footer">
  <div class="abs brand"><i class="dot"></i>Medical Clinics</div>
  <p class="blurb">Lorem Ipsum is simply dummy text of the printing and typesetting industry. Lorem Ipsum has been the industry's standard dummy text ever since</p>
  <div class="abs col" style="left:369px"><h5>Navigation</h5><ul><li style="color:#ddd">Home</li><li>Our Clinic</li><li>Newsletter</li><li>Our Staff</li><li>Resources</li></ul></div>
  <div class="abs col" style="left:549px"><h5>Links</h5><ul><li>Help</li><li>Support</li><li>Privacy Policy</li></ul></div>
  <div class="abs col" style="left:669px"><h5>Contact Us</h5>
    <table class="ct"><tr><td>Telephone :</td><td>604-555-0192</td></tr><tr><td>Email:</td><td>hello@cedarwell.ca</td></tr><tr><td>Address:</td><td>48 Alder Lane<br>Kelton,B. Canada,<br>V2K 4RT</td></tr></table>
  </div>
  <div class="bottom">© 2015 Medical Clinces. All Rights Reservsd
    <div class="mid"><span>About Us</span><span>Terms of Use</span><span>Privacy Policy</span></div>
  </div>
</footer>

</body>
</html>
```